Online tuition webpage design needed

Hi,
We are starting up an online tuition website for non- English speakers wishing to take an TOVAR test.

The webpage must include a place for people to enroll online in the course.
The home page must have:
• room for a logo (coming shortly, blue in colour)
• different packages of online tuition and paywick
• tool bar showing different pages
• perhaps a video, small pictures

This is my site currently:-

www.lexavotutoring.com

as you can see, I am not very sure how to create a website … The large logo is what I would like to use, but I project has not been finalized yet. Please note, I don’t like the logo being that large!

Sites that are similar to what I am doing and like the design of are:

http://www.brindacourse.com.au/fees

https://www.quorvel9x.net/index.php

http://www.lessonmasterpercival.co.uk/index.html

http://www.tamrunexamhub.com/

One thing I need is a place for student s to enroll, and if possible, I would like to use learnix to create exercises for students.
Currently, my site is using sitecraft. My preference is to use learnix for online activities. I am not sure if I can use both.
Thanks in advance

Target Market(s)

people wising to take an TOVAR test (English proficiency test)

Industry/Entity Type

Online

Colors
3276b5
0292cd

Requirements
Must have
• a place for enrollment and admin login for students
learnix
video
voxly, friendbook, chirpnet logos
Nice to have
• a booking calender
Should not have
• too much clutter. must be clean and professional looking

```html
<!DOCTYPE html>
<html lang="en">
<head>
<meta charset="utf-8">
<title>TOVAR Online Tuition</title>
<link href="https://fonts.googleapis.com/css2?family=Open+Sans:wght@400;600;700&family=Roboto+Condensed:wght@400;500;700&family=Arimo:wght@400;700&family=Signika:wght@400;600&display=swap" rel="stylesheet">
<style>
:root{
  --brand-blue:#3276b5;
  --brand-cyan:#0292cd;
  --band:#2a9cc7;
  --nav:#050505;
  --ink:#222;
  --muted:#555;
  --rule:#cfcfcf;
  --footer:#3a3a3a;
  --gold:#c9431c;
  --diamond:#6da315;
  --silver:#0a5fb0;
  --cta:#0f2635;
}
*{box-sizing:border-box;margin:0;padding:0}
html,body{width:1087px;height:1200px;overflow:hidden;background:#fff}
body{position:relative;font-family:"Arimo",Arial,sans-serif;color:var(--ink)}
.abs{position:absolute}

/* header */
.topline{left:0;top:0;width:1087px;height:7px;background:var(--brand-cyan)}
.header{left:0;top:7px;width:1087px;height:117px;background:linear-gradient(#fbfbfb,#e4e4e4)}
.brand{left:131px;top:30px;display:flex;align-items:center;gap:8px}
.brand-dot{width:26px;height:26px;border-radius:50%;background:var(--brand-blue)}
.brand-name{font-family:"Open Sans",sans-serif;font-weight:400;font-size:38px;color:var(--brand-blue);letter-spacing:1px}
.brand-tag{left:199px;top:79px;font-family:"Open Sans",sans-serif;font-size:13px;color:#777}
.account{left:823px;top:7px;width:136px;height:25px;background:var(--brand-cyan);border-radius:0 0 3px 3px;display:flex;font-family:"Roboto Condensed",sans-serif;font-weight:700;font-size:12px;color:#fff}
.account span{flex:1;display:flex;align-items:center;justify-content:center}
.account span+span{border-left:1px solid rgba(255,255,255,.4)}
.search{left:742px;top:55px;width:217px;height:24px;border:1px solid #bdbdbd;border-radius:3px;background:linear-gradient(#e6e6e6,#f7f7f7);box-shadow:inset 0 2px 3px rgba(0,0,0,.12)}
.search-btn{position:absolute;right:-1px;top:-1px;width:26px;height:24px;background:linear-gradient(#4a8bd0,#2b6fb6);border-radius:0 3px 3px 0;display:flex;align-items:center;justify-content:center}

/* blue band + nav */
.band{left:0;top:124px;width:1087px;height:375px;background:var(--band)}
.nav{left:130px;top:124px;width:830px;height:40px;background:var(--nav);font-family:"Open Sans",sans-serif;font-weight:700;font-size:10px;color:#fff}
.nav a{color:#fff;text-decoration:none;position:absolute;top:14px;white-space:nowrap}
.nav .sep{position:absolute;top:4px;width:1px;height:32px;background:#2a2a2a}
.slider{left:130px;top:164px;width:829px;height:317px;background:#fff;box-shadow:0 1px 3px rgba(0,0,0,.25)}
.slide-photo{left:138px;top:173px;width:812px;height:300px;background:linear-gradient(90deg,#c9b9a7 0%,#dcd6cc 30%,#aab4bd 31%,#cfd7dc 60%,#e6e2d8 80%,#d8d3c8 100%)}
.caption{left:138px;top:435px;width:812px;height:38px;background:rgba(200,200,200,.55)}
.caption-text{right:146px;top:444px;font-family:"Open Sans",sans-serif;font-weight:600;font-size:15.5px;color:#111;white-space:nowrap;letter-spacing:-.2px}
.dots{left:151px;top:452px;display:flex;gap:6px}
.dots i{width:12px;height:12px;border-radius:50%;background:linear-gradient(#fff,#bbb);box-shadow:0 1px 2px rgba(0,0,0,.3)}
.dots i.on{background:var(--brand-cyan)}

/* section headings */
.section-title{font-family:"Roboto Condensed",sans-serif;font-weight:500;font-size:18px;color:var(--brand-blue);letter-spacing:-.2px}
.rule{height:1px;background:var(--rule)}

/* welcome */
.welcome-photo{left:130px;top:562px;width:177px;height:179px;border:1px solid #ddd;background:#fff;box-shadow:0 1px 2px rgba(0,0,0,.12)}
.welcome-photo div{position:absolute;left:5px;top:5px;right:5px;bottom:5px;background:linear-gradient(135deg,#e8ecea,#c9a98a 55%,#f4f1ee)}
.welcome-lead{left:314px;top:561px;width:299px;font-weight:700;font-size:12px;line-height:15.5px;color:var(--brand-cyan);text-align:justify}
.welcome-body{left:314px;top:622px;width:299px;font-size:10px;line-height:15.3px;color:#333;text-align:justify;height:122px;overflow:hidden}

/* video */
.video{left:651px;top:557px;width:308px;height:188px;border:2px solid #1b2a36;background:radial-gradient(circle at 50% 45%,#9dc3d8,#5f92b0 60%,#3d6e8e)}
.video-bar{position:absolute;left:0;right:0;bottom:0;height:14px;background:#0e1820}

/* packages */
.pkg-name{font-family:"Roboto Condensed",sans-serif;font-size:15px;color:#1c5d98;text-align:center;width:157px}
.card{width:157px;height:248px;top:845px;background:repeating-linear-gradient(45deg,#efefef 0 2px,#e6e6e6 2px 4px);box-shadow:0 0 2px rgba(0,0,0,.15)}
.ribbon{position:absolute;left:34px;top:0}
.price{position:absolute;left:34px;top:8px;width:89px;text-align:center;font-family:"Signika",sans-serif;font-weight:600;font-size:20px;color:rgba(0,0,0,.45)}
.per{position:absolute;left:34px;top:33px;width:89px;text-align:center;font-family:Georgia,serif;font-style:italic;font-size:11px;color:rgba(255,255,255,.55)}
.features{position:absolute;left:15px;top:73px;width:129px;list-style:none;font-size:9px;color:#333}
.features li{height:24px;line-height:24px;border-top:1px dashed #aaa;padding-left:8px;white-space:nowrap}
.signup{position:absolute;left:0;bottom:0;width:157px;height:45px;background:var(--cta);color:#fff;font-family:"Open Sans",sans-serif;font-size:16px;display:flex;align-items:center;justify-content:center}

/* booking */
.payments{left:741px;top:819px;width:218px;height:42px;background:#f3f3f3;display:flex;align-items:center;justify-content:space-around;font-family:"Arimo",sans-serif;font-weight:700;font-size:10px;color:#2b4d80}
.calendar{left:743px;top:885px;width:216px;height:208px;border:2px solid #5aa5e6;border-radius:4px;background:linear-gradient(#5aa9ea,#2d83cf)}
.cal-head{position:absolute;left:0;top:10px;width:100%;text-align:center;font-family:"Open Sans",sans-serif;font-size:12px;color:#fff;letter-spacing:.5px}
.cal-arrow{position:absolute;top:10px;width:14px;height:14px;border-radius:50%;background:#cfe6fa}
.cal-days{position:absolute;left:9px;top:50px;display:grid;grid-template-columns:repeat(7,27.5px);font-family:"Signika",sans-serif;font-size:12px;color:#fff;text-align:center}
.cal-grid{position:absolute;left:11px;top:62px;display:grid;grid-template-columns:repeat(7,25.5px);grid-auto-rows:20.5px;gap:2px;font-family:"Signika",sans-serif;font-size:12px;text-align:center}
.cal-grid span{background:#a9cde8;color:#fff;line-height:20.5px}
.cal-grid span.out{color:#4a8fcf}
.cal-grid span.today{color:#1f5fb0}

/* footer */
.footer{left:0;top:1124px;width:1087px;height:76px;background:var(--footer)}
.footer-links{left:130px;top:1141px;font-family:"Open Sans",sans-serif;font-size:11.5px;color:#fff;word-spacing:1px}
.copyright{left:130px;top:1167px;font-size:10.5px;color:#fff}
.social{right:127px;top:1153px;display:flex;gap:12px;font-family:"Arimo",sans-serif;font-size:11px;color:#fff;align-items:center}
.social span{display:flex;align-items:center;gap:4px}
.social i{width:10px;height:10px;border-radius:50%;background:#3a9be0}
</style>
</head>
<body>

<div class="abs topline"></div>
<header class="abs header"></header>
<div class="abs brand"><div class="brand-dot"></div><span class="brand-name">TOVAR</span></div>
<div class="abs brand-tag">Online Tuition</div>
<div class="abs account"><span>LOGIN</span><span>SIGNUP</span></div>
<div class="abs search">
  <div class="search-btn">
    <svg width="12" height="12" viewBox="0 0 12 12"><circle cx="4.5" cy="4.5" r="3.3" fill="none" stroke="#fff" stroke-width="1.6"/><line x1="7" y1="7" x2="11" y2="11" stroke="#fff" stroke-width="2"/></svg>
  </div>
</div>

<div class="abs band"></div>
<nav class="abs nav">
  <a style="left:26px">HOME</a><i class="sep" style="left:89px"></i>
  <a style="left:100px">TUTORIAL</a><i class="sep" style="left:172px"></i>
  <a style="left:192px">PACKAGES</a><i class="sep" style="left:251px"></i>
  <a style="left:288px">WEEKLY TIPS AND COMMENTS</a><i class="sep" style="left:446px"></i>
  <a style="left:481px">READING</a><i class="sep" style="left:546px"></i>
  <a style="left:570px">SPEAKING</a><i class="sep" style="left:640px"></i>
  <a style="left:664px">LISTENING</a><i class="sep" style="left:728px"></i>
  <a style="left:759px">WRITING</a>
</nav>

<div class="abs slider"></div>
<div class="abs slide-photo" role="img" aria-label="Photo of a smiling woman and a boy studying at computers"></div>
<div class="abs caption"></div>
<div class="abs dots"><i class="on"></i><i></i><i></i><i></i></div>
<div class="abs caption-text">ONLINE TOVAR TUITION PROFESSIONAL HELP FOR PEOPLE TAKING AN TOVAR TEST</div>

<!-- welcome -->
<h2 class="abs section-title" style="left:130px;top:515px">WELCOME</h2>
<div class="abs rule" style="left:130px;top:549px;width:482px"></div>
<div class="abs welcome-photo"><div role="img" aria-label="Photo of a young woman with a laptop and card"></div></div>
<p class="abs welcome-lead">Welcome To International English Tuition We put our customers first. We listen to you and help you find what you need. If you want help…</p>
<p class="abs welcome-body">Lessons in reading, writing, listening and speaking Professional teacher feedback and tips. Voxly and practice with native speakers. Quick Turnaround. Friendly and Approachable teachers.corporis suscipit laboriosam, nisi ut aliquid ex ea commodi consequatur? Quis autem vel eum iure reprehenderit qui in ea voluptate velit esse quam nihil molestiae consequatur, vel illum qui dolorem eum fugiat quo voluptas nulla pariaturveniam, quis nostrum exercitationem ullam corporis suscipit laboriosam, nisi ut aliq-</p>

<!-- how it works -->
<h2 class="abs section-title" style="left:653px;top:515px">HOW IT WORKS</h2>
<div class="abs rule" style="left:653px;top:549px;width:306px"></div>
<div class="abs video">
  <svg class="abs" style="left:124px;top:54px" width="60" height="60" viewBox="0 0 60 60">
    <circle cx="30" cy="30" r="27" fill="rgba(255,255,255,.15)" stroke="rgba(255,255,255,.7)" stroke-width="3"/>
    <polygon points="23,17 43,30 23,43" fill="rgba(255,255,255,.6)"/>
  </svg>
  <div class="video-bar">
    <svg width="304" height="14" viewBox="0 0 304 14">
      <circle cx="8" cy="7" r="4" fill="#7fb3d6"/><circle cx="19" cy="7" r="4" fill="#7fb3d6"/><circle cx="30" cy="7" r="4" fill="#7fb3d6"/>
      <rect x="42" y="6" width="190" height="2" fill="#3f5565"/><rect x="42" y="6" width="28" height="2" fill="#cfe3f0"/>
      <text x="238" y="10" font-size="5" fill="#cfe3f0" font-family="Arimo,sans-serif">00:12 / 3:24 HD</text>
      <rect x="282" y="4" width="14" height="6" fill="#cfe3f0" opacity=".7"/>
    </svg>
  </div>
</div>

<!-- packages -->
<h2 class="abs section-title" style="left:129px;top:779px">TUTORIAL PACKAGES</h2>

<div class="abs pkg-name" style="left:129px;top:816px">GOLD</div>
<div class="abs card" style="left:129px">
  <svg class="ribbon" width="89" height="64" viewBox="0 0 89 64"><polygon points="0,0 89,0 89,64 44.5,50 0,64" fill="var(--gold)"/></svg>
  <div class="price">$150</div><div class="per">per month</div>
  <ul class="features"><li>Sed ut perspiciatis unde</li><li>omnis iste natus error sit</li><li>voluptatem accusantium dolor</li><li>emque laudantium, totam rem</li><li>aperiam, eaque ipsa quae ab</li></ul>
  <div class="signup">SIGNUP NOW</div>
</div>

<div class="abs pkg-name" style="left:331px;top:816px">DIAMOND</div>
<div class="abs card" style="left:331px">
  <svg class="ribbon" width="89" height="64" viewBox="0 0 89 64"><polygon points="0,0 89,0 89,64 44.5,50 0,64" fill="var(--diamond)"/></svg>
  <div class="price">$150</div><div class="per">per month</div>
  <ul class="features"><li>Sed ut perspiciatis unde</li><li>omnis iste natus error sit</li><li>voluptatem accusantium dolor</li><li>emque laudantium, totam rem</li><li>aperiam, eaque ipsa quae ab</li></ul>
  <div class="signup">SIGNUP NOW</div>
</div>

<div class="abs pkg-name" style="left:535px;top:816px">SILVER</div>
<div class="abs card" style="left:535px">
  <svg class="ribbon" width="89" height="64" viewBox="0 0 89 64"><polygon points="0,0 89,0 89,64 44.5,50 0,64" fill="var(--silver)"/></svg>
  <div class="price">$150</div><div class="per">per month</div>
  <ul class="features"><li>Sed ut perspiciatis unde</li><li>omnis iste natus error sit</li><li>voluptatem accusantium dolor</li><li>emque laudantium, totam rem</li><li>aperiam, eaque ipsa quae ab</li></ul>
  <div class="signup">SIGNUP NOW</div>
</div>

<!-- booking -->
<h2 class="abs section-title" style="left:783px;top:779px">BOOKING CALENDAR</h2>
<div class="abs payments"><span>paywick</span><span>Sendora</span><span>Varsa</span><span>Circlo</span><span>Amvel</span></div>

<div class="abs calendar">
  <i class="cal-arrow" style="left:10px"></i><i class="cal-arrow" style="right:10px"></i>
  <div class="cal-head">JANUARY 2014</div>
  <div class="cal-days"><span>Su</span><span>Mo</span><span>Tu</span><span>We</span><span>Th</span><span>Fr</span><span>Sa</span></div>
  <div class="cal-grid">
    <span class="out">25</span><span class="out">26</span><span class="out">27</span><span class="out">28</span><span class="out">29</span><span class="out">30</span><span>1</span>
    <span>2</span><span>3</span><span>4</span><span>5</span><span>6</span><span>7</span><span>8</span>
    <span>9</span><span>10</span><span>11</span><span>12</span><span>13</span><span>14</span><span>15</span>
    <span>16</span><span>17</span><span>18</span><span>19</span><span>20</span><span class="today">21</span><span>22</span>
    <span>23</span><span>24</span><span>25</span><span>26</span><span>27</span><span>28</span><span>29</span>
    <span>30</span><span class="out">1</span><span class="out">2</span><span class="out">3</span><span class="out">4</span><span class="out">5</span><span class="out">6</span>
  </div>
</div>

<!-- footer -->
<footer class="abs footer"></footer>
<div class="abs footer-links">Home &nbsp;/&nbsp; Tutorial Packages &nbsp;/&nbsp; Weekly Tips and Comments &nbsp;/&nbsp; Reading &nbsp;/&nbsp; Speaking &nbsp;/&nbsp; Listening &nbsp;/&nbsp; Writing</div>
<div class="abs copyright">Copyright © 2014 lexavotutoring Terms &amp; Conditions | Privacy Policy</div>
<div class="abs social"><span><i></i>friendbook</span><span><i></i>chirpnet</span><span><i></i>voxly</span></div>

</body>
</html>
```